Professional Package for CPA Firm

We would like a stationery design for our new CPA Firm based in Atlanta, GA called 'Vale 8'. We work with investors to help grow investments, tax free. We would like the design to have a professional/minimal look with a 'wow' factor. We need 9.5″ x 4.125″, 9x12, and 10x13 mailing envelopes, business cards, and a letterhead. We have a logo that is already complete. For the letterhead, we would like to have space to put credentials at the bottom of the page

Industry/Entity Type

CPA, Accounting

```html
<!DOCTYPE html>
<html lang="en">
<head>
<meta charset="utf-8">
<title>Vale 8 Stationery</title>
<link href="https://fonts.googleapis.com/css2?family=Open+Sans:ital,wght@0,400;0,600;0,700;1,400&family=Roboto:ital,wght@0,400;0,700;1,400&display=swap" rel="stylesheet">
<style>
:root{
  --bg:#e9e9e9;
  --paper:#f2f2f2;
  --ink:#1d1d1b;
  --text:#4a4a4a;
  --blue:#2593cc;
  --dark:#222629;
  --rule:#d8d8d8;
}
*{margin:0;padding:0;box-sizing:border-box}
html,body{width:1200px;height:795px;overflow:hidden}
body{background:var(--bg);position:relative;font-family:"Open Sans",sans-serif;color:var(--text)}
.sheet{position:absolute;background:var(--paper)}

/* brand lockup */
.brand{position:absolute;text-align:center;line-height:1}
.brand-row{display:flex;align-items:center;justify-content:center;gap:3px}
.brand-mark{background:var(--blue);display:block}
.brand-name{font-family:"Roboto",sans-serif;font-weight:700;color:var(--ink);letter-spacing:.5px}
.brand-tag{font-family:"Open Sans",sans-serif;color:var(--ink);letter-spacing:.4px;display:block}

/* letterhead */
.letterhead{left:292px;top:99px;width:293px;height:414px}
.letterhead .brand{left:0;width:100%;top:44px}
.letterhead .brand-mark{width:10px;height:10px}
.letterhead .brand-name{font-size:18px}
.letterhead .brand-tag{font-size:5px;margin-top:2px}
.letter-body{position:absolute;left:26px;top:97px;width:240px;font-size:5.3px;line-height:8px}
.letter-body p{text-align:justify;margin-bottom:8px}
.signature{display:block;width:34px;height:32px;background:#e4e4e4;margin-top:4px}
.letter-footer{position:absolute;left:0;width:100%;top:371px;text-align:center;font-family:"Roboto",sans-serif;font-size:5.6px;line-height:8px;color:#555}
.letter-footer .contacts{display:flex;justify-content:center;gap:3px;align-items:center}
.letter-footer svg{width:5px;height:5px;vertical-align:middle;margin-right:1px}
.credentials{color:var(--blue);font-style:italic}

/* presentation folder */
.folder{left:637px;top:80px;width:346px;height:436px}
.folder-spine{position:absolute;top:0;bottom:0;width:1px;background:var(--rule)}
.folder-photo{position:absolute;left:0;top:64px;width:346px;height:283px;background:linear-gradient(135deg,#e6e9ec 0%,#c9cfd5 45%,#6b7580 75%,#3b4652 100%)}
.folder-shapes{position:absolute;left:0;top:64px}
.folder .brand{right:24px;top:366px}
.folder .brand-mark{width:9px;height:9px}
.folder .brand-name{font-size:17px}
.folder .brand-tag{font-size:4.8px;margin-top:2px}

/* business cards */
.card{left:186px;width:133px;height:75px}
.card-front{top:550px}
.card-back{top:646px}
.card .brand{left:18px;top:26px}
.card .brand-mark{width:5px;height:5px}
.card .brand-name{font-size:10px}
.card .brand-tag{font-size:2.6px;margin-top:1px}
.card-divider{position:absolute;left:63px;top:21px;width:1px;height:33px;background:var(--blue)}
.card-details{position:absolute;left:70px;top:21px;font-family:"Roboto",sans-serif;font-size:3.2px;line-height:4.4px;color:#333}
.card-name{font-weight:700;font-size:4px;color:var(--ink)}
.card-role{margin-bottom:2px}

/* envelopes */
.envelope{top:561px;height:157px;width:329px}
.envelope-front{left:353px}
.envelope-front .brand{left:23px;top:23px}
.envelope-front .brand-mark{width:8px;height:8px}
.envelope-front .brand-name{font-size:15px}
.envelope-front .brand-tag{font-size:4.4px;margin-top:1px}
.return-address{font-family:"Roboto",sans-serif;font-size:5px;line-height:6px;color:#444;margin-top:2px}
.envelope-back{left:714px;width:328px}
.envelope-flap{position:absolute;left:0;top:0}
</style>
</head>
<body>

<section class="sheet letterhead">
  <div class="brand">
    <div class="brand-row"><span class="brand-mark"></span><span class="brand-name">Vale 8</span></div>
    <span class="brand-tag">CPAs and Tax Advisors</span>
  </div>
  <div class="letter-body">
    <p>Dear customer,</p>
    <p>Lorem ipsum dolor sit amet, consectetur adipisicing elit, sed do eiusmod tempor incididunt ut labore et dolore magna aliqua. Ut enim ad minim veniam, quis nostrud exercitation ullamco laboris nisi ut aliquip ex ea commodo consequat. Duis aute irure dolor in reprehenderit in voluptate velit esse cillum dolore eu fugiat nulla pariatur. Excepteur sint occaecat cupidatat non proident, sunt in culpa qui officia deserunt mollit anim id est laborum.</p>
    <p>Lorem ipsum dolor sit amet, consectetur adipisicing elit, sed do eiusmod tempor incididunt ut labore et dolore magna aliqua. Ut enim ad minim veniam, quis nostrud exercitation ullamco laboris nisi ut aliquip ex ea commodo consequat. Duis aute irure dolor in reprehenderit in voluptate velit esse cillum dolore eu fugiat nulla pariatur. Excepteur sint occaecat cupidatat non proident, sunt in culpa qui officia deserunt mollit anim id est laborum.</p>
    <p>Lorem ipsum dolor sit amet, consectetur adipisicing elit, sed do eiusmod tempor incididunt ut labore et dolore magna aliqua. Ut enim ad minim veniam, quis nostrud exercitation ullamco laboris nisi ut aliquip ex ea commodo consequat. Duis aute irure dolor in reprehenderit in voluptate velit esse cillum dolore eu fugiat nulla pariatur. Excepteur sint occaecat cupidatat non proident, sunt in culpa qui officia deserunt mollit anim id est laborum.</p>
    <p>Lorem ipsum dolor sit amet, consectetur adipisicing elit, sed do eiusmod tempor incididunt ut labore et dolore magna aliqua. Ut enim ad minim veniam, quis nostrud exercitation ullamco laboris nisi ut aliquip ex ea commodo consequat. Duis aute irure dolor in reprehenderit.</p>
    <p style="margin-bottom:0">Yours Sincerely,</p>
    <span class="signature" role="img" aria-label="Handwritten signature of the managing partner"></span>
  </div>
  <footer class="letter-footer">
    <div>2180 Linden Avenue, Suite 210B, Atlanta, GA 30318</div>
    <div class="contacts">
      <span><svg viewBox="0 0 10 10"><path d="M2 1l2 0 1 2.5-1.2 1a6 6 0 0 0 2.7 2.7l1-1.2 2.5 1v2c0 .5-.5 1-1 1A8 8 0 0 1 1 2c0-.5.5-1 1-1z" fill="#333"/></svg>404-555-0192</span>
      <span><svg viewBox="0 0 10 10"><rect x="0.5" y="2" width="9" height="6.5" fill="#333"/><path d="M0.5 2l4.5 3.5L9.5 2" stroke="#f2f2f2" stroke-width=".8" fill="none"/></svg>team@vale8cpas.com</span>
      <span><svg viewBox="0 0 10 10"><circle cx="5" cy="5" r="4.2" fill="none" stroke="#333"/><path d="M1 5h8M5 .8c2 2.5 2 5.9 0 8.4M5 .8c-2 2.5-2 5.9 0 8.4" stroke="#333" stroke-width=".7" fill="none"/></svg>www.vale8cpas.com</span>
    </div>
    <div class="credentials">Member of the Regional Society and National Guild of CPAs</div>
  </footer>
</section>

<section class="sheet folder">
  <span class="folder-spine" style="left:7px"></span>
  <span class="folder-spine" style="left:19px"></span>
  <div class="folder-photo" role="img" aria-label="Photograph of three colleagues talking around a meeting table in a bright office"></div>
  <svg class="folder-shapes" width="346" height="283" viewBox="0 0 346 283">
    <polygon points="251,0 346,0 346,283" fill="var(--blue)" opacity=".92"/>
    <polygon points="0,18 0,283 88,283" fill="var(--dark)" opacity=".9"/>
  </svg>
  <div class="brand">
    <div class="brand-row"><span class="brand-mark"></span><span class="brand-name">Vale 8</span></div>
    <span class="brand-tag">CPAs and Tax Advisors</span>
  </div>
</section>

<section class="sheet card card-front">
  <div class="brand">
    <div class="brand-row"><span class="brand-mark"></span><span class="brand-name">Vale 8</span></div>
    <span class="brand-tag">CPAs and Tax Advisors</span>
  </div>
  <span class="card-divider"></span>
  <div class="card-details">
    <div class="card-name">SAM REYES, CPA</div>
    <div class="card-role">Managing Partner</div>
    <div>2180 Linden Avenue, Suite</div>
    <div>210B, Atlanta, GA 30318</div>
    <div>404-555-0192</div>
    <div>samreyes@vale8cpas.com</div>
    <div>www.vale8cpas.com</div>
  </div>
</section>
<section class="sheet card card-back"></section>

<section class="sheet envelope envelope-front">
  <div class="brand">
    <div class="brand-row"><span class="brand-mark"></span><span class="brand-name">Vale 8</span></div>
    <span class="brand-tag">CPAs and Tax Advisors</span>
    <div class="return-address">2180 Linden Avenue, Suite<br>210B, Atlanta, GA 30318</div>
  </div>
</section>

<section class="sheet envelope envelope-back">
  <svg class="envelope-flap" width="328" height="157" viewBox="0 0 328 157">
    <path d="M1 4 L7 55 L321 55 L327 4" fill="none" stroke="var(--rule)" stroke-width="1"/>
  </svg>
</section>

</body>
</html>
```